Plakat-Design Workshop gegen Prüfungsangst
Zielgruppe
Prüfungsangst überwinden mittels Workshops: 'Selbsthypnose erlernen'
Zielgruppe Studenten
Schweißausbrüche, Blackout, und Resignation.
Viele kennen diese unangenehmen Momente, wenn eine Prüfung begonnen hat und die Aufgabenstellungen scheinbar unlösbar sind.
Dann ist Entspannung nahezu unmöglich. Das Stresshormon Cortisol wurde bereits ausgeschüttet. Es beeinträchtigt die Erinnerung an das Gelernte.
Die mentale Vorbereitung sollte schon viel eher ansetzen, wenn es noch nicht zu spät ist. Wenn der Körper noch nicht verkrampft ist.
Selbsthypnose vor Prüfungen ist hier eine tolle Möglichkeit.
Mit Hilfe einer geführten Selbsthypnoseanleitung ist es Dir möglich Dein Unterbewusstsein so zu programmieren, dass diese Übererregungszustände vor Prüfungssituationen deutlich reduziert werden.
Aufgabenstellung
DINA 4 Plakat, 'Prüfungsangst?' mit einem Freifeld, wo man Ort, Datum und Zeit der Veranstaltung 'Selbsthypnose erlernen'
(Selbstsicher in die Prüfung) eindrucken kann.
darunter:
Anmeldung: Tel: 01563 8074215
Dipl. Sportl. Henrik Wolde Mentaltraining
weitere Infos auch über Einzelsitzungen: www.wolde-trancepraxis.de

```html
<!DOCTYPE html>
<html lang="de">
<head>
<meta charset="utf-8">
<title>Prüfungsangst? – Workshop Selbsthypnose</title>
<link href="https://fonts.googleapis.com/css2?family=Montserrat:wght@400;500;700&display=swap" rel="stylesheet">
<style>
  :root {
    --ink: #000000;
    --paper: #ffffff;
    --accent: #e53935;
    --photo-warm: #b86a2c;
    --photo-deep: #7a3f17;
    --photo-cool: #9fb0c8;
  }
  * { margin: 0; padding: 0; box-sizing: border-box; }
  html, body { width: 848px; height: 1200px; overflow: hidden; background: var(--paper); }
  .poster {
    position: relative;
    width: 848px;
    height: 1200px;
    overflow: hidden;
    background: var(--paper);
    font-family: "Montserrat", sans-serif;
    color: var(--ink);
  }
  .hero-photo {
    position: absolute;
    left: 0; top: 0;
    width: 848px; height: 546px;
    background:
      radial-gradient(ellipse 260px 300px at 620px 330px, var(--photo-cool) 0%, rgba(159,176,200,0.55) 45%, rgba(159,176,200,0) 75%),
      linear-gradient(100deg, var(--photo-deep) 0%, var(--photo-warm) 40%, #c98446 70%, #a85e26 100%);
  }
  .headline-bar {
    position: absolute;
    left: 0; top: 486px;
    width: 609px; height: 105px;
    background: var(--ink);
  }
  .headline {
    position: absolute;
    left: 84px; top: 506px;
    font-size: 57px;
    font-weight: 500;
    letter-spacing: 3px;
    color: var(--paper);
    line-height: 1;
  }
  .title-frame { position: absolute; left: 66px; top: 660px; width: 648px; height: 56px; }
  .workshop-title {
    position: absolute;
    left: 77px; top: 664px;
    font-size: 50px;
    font-weight: 700;
    line-height: 1;
    letter-spacing: 0.3px;
  }
  .workshop-subtitle {
    position: absolute;
    left: 77px; top: 714px;
    font-size: 36px;
    font-weight: 400;
    color: var(--accent);
    line-height: 1;
    letter-spacing: 0.5px;
  }
  .trainer {
    position: absolute;
    left: 81px; top: 806px;
    font-size: 26px;
    line-height: 31px;
  }
  .trainer strong { font-weight: 700; display: block; }
  .event-fields {
    position: absolute;
    left: 518px; top: 806px;
    width: 280px;
  }
  .event-field {
    display: flex;
    align-items: flex-end;
    height: 55px;
    font-size: 24px;
    line-height: 1;
  }
  .event-field .blank {
    flex: 1;
    border-bottom: 1.5px solid var(--ink);
    margin-left: 14px;
    margin-bottom: 3px;
  }
  .footer-wave { position: absolute; left: 0; top: 895px; width: 848px; height: 305px; }
  .registration {
    position: absolute;
    left: 81px; top: 1005px;
    font-size: 24px;
    line-height: 29px;
    color: var(--paper);
    letter-spacing: 0.5px;
  }
  .contact {
    position: absolute;
    left: 86px;
    display: flex;
    align-items: center;
    gap: 18px;
    font-size: 25px;
    color: var(--paper);
    letter-spacing: 1px;
  }
  .contact svg { width: 24px; height: 24px; flex: none; }
  .contact-phone { top: 1086px; }
  .contact-web { top: 1134px; }
  .brand {
    position: absolute;
    left: 489px; top: 1033px;
    width: 311px; height: 138px;
    display: flex;
    align-items: center;
    justify-content: center;
    gap: 10px;
    font-size: 22px;
    font-weight: 700;
    color: var(--paper);
    letter-spacing: 0.5px;
  }
  .brand-dot { width: 14px; height: 14px; border-radius: 50%; background: var(--accent); }
</style>
</head>
<body>
<div class="poster">
  <div class="hero-photo" role="img" aria-label="Foto: Studentin stützt in einer Prüfung gestresst den Kopf in die Hände, dahinter schreibende Mitschüler"></div>

  <div class="headline-bar"></div>
  <h1 class="headline">Prüfungsangst?</h1>

  <svg class="title-frame" viewBox="0 0 648 56" aria-hidden="true">
    <path d="M1 14 V1 H13" fill="none" stroke="#000" stroke-width="1.5"/>
    <path d="M647 42 V55 H635" fill="none" stroke="#000" stroke-width="1.5"/>
  </svg>
  <h2 class="workshop-title">Workshop Selbsthypnose</h2>
  <p class="workshop-subtitle">Selbstsicher in die Prüfung</p>

  <p class="trainer">Dipl. Sportl.<strong>Henrik Wolde Mentaltraining</strong></p>

  <div class="event-fields">
    <div class="event-field">Ort:<span class="blank"></span></div>
    <div class="event-field">Datum:<span class="blank"></span></div>
    <div class="event-field">Uhrzeit:<span class="blank"></span></div>
  </div>

  <svg class="footer-wave" viewBox="0 0 848 305" preserveAspectRatio="none" aria-hidden="true">
    <path d="M0 4 C150 70 450 95 848 98 V305 H0 Z" fill="#000"/>
  </svg>

  <p class="registration">Anmeldung<br>und weitere Infos unter:</p>

  <div class="contact contact-phone">
    <svg viewBox="0 0 24 24" aria-hidden="true"><path d="M6.5 2.5 L9.5 6.5 L7.8 9 C9 11.8 12 14.8 15 16.2 L17.5 14.5 L21.5 17.5 L19.5 21 C11 21 3 13 3 4.5 Z" fill="none" stroke="#e53935" stroke-width="2" stroke-linejoin="round"/></svg>
    <span>01563 8074215</span>
  </div>
  <div class="contact contact-web">
    <svg viewBox="0 0 24 24" aria-hidden="true"><g fill="none" stroke="#e53935" stroke-width="2"><circle cx="12" cy="12" r="10"/><ellipse cx="12" cy="12" rx="4.5" ry="10"/><path d="M2 12 H22"/></g></svg>
    <span>www.wolde-trancepraxis.de</span>
  </div>

  <div class="brand"><span class="brand-dot"></span>Wolde-Trancepraxis</div>
</div>
</body>
</html>
```